Refresh Application User Interface

Brightmoor wishes to update the look of its business applications. Two representative forms are shown below. Please note, we are not considering changes in functionality or usability. Our goal is a cleaner, more contemporary design.

Industry/Entity Type

Business

```html
<!DOCTYPE html>
<html lang="en">
<head>
<meta charset="utf-8">
<title>Purchase Order – Brightmoor eBuy</title>
<link href="https://fonts.googleapis.com/css2?family=Open+Sans:wght@300;400;600;700&display=swap" rel="stylesheet">
<style>
:root{
  --topbar:#33373d;
  --blue:#4a90e2;
  --blue-dark:#2f6fc4;
  --brand:#1a4fa0;
  --text:#3a3d42;
  --muted:#8d97a8;
  --label:#555a61;
  --border:#dcdfe4;
  --panel:#f4f5f7;
  --tabs:#eef0f3;
  --green:#5cc15c;
  --red:#f0506e;
  --orange:#f0a500;
  --white:#fff;
}
*{box-sizing:border-box;margin:0;padding:0}
html,body{width:1200px;height:861px;overflow:hidden}
body{position:relative;background:var(--white);font-family:"Open Sans",sans-serif;color:var(--text)}
.a{position:absolute;white-space:nowrap}
.topbar{left:0;top:0;width:1200px;height:54px;background:var(--topbar);color:#e8eaed;font-size:17px;font-weight:300}
.topbar b{font-weight:600}
.topbar .v{top:14px}
.nav-main{font-size:24px;font-weight:300;color:#4a4e55;top:76px}
.nav-main .sep{color:#9aa0a8}
.nav-main .active{color:var(--blue-dark);font-weight:600}
.brand{left:998px;top:76px;font-size:27px;font-weight:700;color:var(--brand);letter-spacing:1px}
.nav-sub{top:133px;font-size:21px;font-weight:300;color:var(--muted)}
.nav-sub .active{color:#2c2f33}
.rule{left:0;top:180px;width:1200px;height:1px;background:var(--border)}
.title{left:26px;top:196px;font-size:24px;color:#222}
.doc-tabs{left:793px;top:207px;width:407px;height:29px;background:var(--tabs);font-size:12px;color:#555}
.doc-tab{position:absolute;top:7px}
.doc-tab.header{left:0;top:0;width:101px;height:29px;background:var(--blue);color:#fff;text-align:center;line-height:29px}
.actionbar{left:0;top:236px;width:1200px;height:27px;background:var(--blue);color:#fff;font-size:15px;font-weight:300}
.actionbar .a{top:3px}
.lbl{font-size:14.5px;color:var(--label)}
.r{text-align:right}
.field{position:absolute;height:27px;border:1px solid var(--border);background:#fff;font-size:12px;padding:5px 10px;color:#333;white-space:nowrap}
.field.focus{border-color:var(--blue)}
.select::after{content:"";position:absolute;right:0;top:0;width:17px;height:100%;background:#eceef1;border-left:1px solid var(--border)}
.select::before{content:"";position:absolute;right:5px;top:11px;border:4px solid transparent;border-top:5px solid #666;z-index:1}
.link{font-size:14.5px;color:var(--blue-dark)}
.panel{left:0;top:529px;width:1200px;height:281px;background:var(--panel)}
.section-tab{top:541px;font-size:16px;font-weight:300;color:var(--muted)}
.section-tab.active{color:#222;font-weight:400}
.footer-rule{left:0;top:810px;width:1200px;height:1px;background:var(--border)}
.status{left:550px;top:825px;font-size:20px;font-weight:300;color:var(--muted)}
svg{position:absolute;overflow:visible}
</style>
</head>
<body>

<header class="a topbar">
  <span class="a v" style="left:15px">Logged In As <b>Dana Reyes</b></span>
  <svg style="left:213px;top:20px" width="14" height="14" viewBox="0 0 14 14"><circle cx="7" cy="7" r="5" fill="none" stroke="#fff" stroke-width="3" stroke-dasharray="2.5 1.5"/><circle cx="7" cy="7" r="1.5" fill="#fff"/></svg>
  <span class="a v" style="left:249px">Current Role <b>administrator</b></span>
  <svg style="left:472px;top:20px" width="13" height="13"><circle cx="6.5" cy="6.5" r="6.5" fill="#fff"/><path d="M3.5 5l3 3 3-3" fill="none" stroke="var(--topbar)" stroke-width="1.8"/></svg>
  <svg style="left:814px;top:12px" width="24" height="30" viewBox="0 0 24 30"><path d="M8 16V4a2 2 0 014 0v9m0-2a2 2 0 014 0v2m0-1a2 2 0 014 0v7c0 5-3 8-8 8s-7-3-9-7l-2-4a2 2 0 013-2l2 3" fill="none" stroke="#fff" stroke-width="1.5"/></svg>
  <svg style="left:856px;top:14px" width="30" height="26"><rect x="1" y="5" width="22" height="16" fill="none" stroke="#fff" stroke-width="1.5"/><rect x="5" y="1" width="22" height="16" fill="var(--topbar)" stroke="#fff" stroke-width="1.5"/><circle cx="25" cy="21" r="5" fill="var(--green)"/><path d="M25 18v6M22 21h6" stroke="#fff" stroke-width="1.5"/></svg>
  <span class="a v" style="left:897px">New Tab</span>
  <svg style="left:984px;top:12px" width="29" height="29"><circle cx="14.5" cy="14.5" r="13.5" fill="none" stroke="#fff" stroke-width="1.5"/><text x="14.5" y="20" text-anchor="middle" fill="#fff" font-size="16" font-family="Open Sans,sans-serif">?</text></svg>
  <svg style="left:1030px;top:12px" width="30" height="30"><path d="M6 15a9 9 0 0118 0" fill="none" stroke="#fff" stroke-width="1.5"/><rect x="3" y="14" width="5" height="9" rx="2" fill="none" stroke="#fff" stroke-width="1.5"/><rect x="22" y="14" width="5" height="9" rx="2" fill="none" stroke="#fff" stroke-width="1.5"/><path d="M24 23c0 3-3 4-7 4" fill="none" stroke="#fff" stroke-width="1.5"/></svg>
  <svg style="left:1081px;top:11px" width="28" height="30"><path d="M14 2H2v26h12" fill="none" stroke="var(--red)" stroke-width="1.5"/><path d="M9 15h17m-5-5l5 5-5 5" fill="none" stroke="var(--red)" stroke-width="1.5"/></svg>
  <span class="a v" style="left:1119px;color:var(--red)">Log Out</span>
</header>

<nav class="nav-main">
  <span class="a nav-main" style="left:27px">Home</span>
  <span class="a nav-main sep" style="left:116px">|</span>
  <span class="a nav-main" style="left:150px">eSource</span>
  <span class="a nav-main sep" style="left:263px">|</span>
  <span class="a nav-main active" style="left:296px">eBuy</span>
  <span class="a nav-main sep" style="left:376px">|</span>
  <span class="a nav-main" style="left:408px">eRequest</span>
  <span class="a nav-main sep" style="left:535px">|</span>
  <span class="a nav-main" style="left:568px">eStock</span>
  <span class="a nav-main sep" style="left:667px">|</span>
  <span class="a nav-main" style="left:699px">ePlan</span>
  <span class="a nav-main sep" style="left:784px">|</span>
  <span class="a nav-main" style="left:815px">Preferences</span>
</nav>
<div class="a brand">BRIGHTMOOR</div>

<nav>
  <span class="a nav-sub active" style="left:27px">Orders</span>
  <span class="a nav-sub" style="left:118px">Receipts</span>
  <span class="a nav-sub" style="left:227px">Shipments</span>
  <span class="a nav-sub" style="left:356px">Invoices</span>
  <span class="a nav-sub" style="left:460px">Pricing</span>
  <span class="a nav-sub" style="left:555px">Tables</span>
  <span class="a nav-sub" style="left:642px">Reports</span>
  <span class="a nav-sub" style="left:742px">Inquiries</span>
  <span class="a nav-sub" style="left:853px">Periodic Tasks</span>
  <span class="a nav-sub" style="left:1014px">Workflows</span>
</nav>
<div class="a" style="left:27px;top:175px;width:63px;height:4px;background:var(--blue-dark)"></div>
<div class="a rule"></div>

<h1 class="a title" style="font-weight:400">Purchase Order</h1>
<div class="a doc-tabs">
  <span class="doc-tab header">Header</span>
  <svg style="left:125px;top:9px" width="12" height="12"><circle cx="6" cy="6" r="6" fill="var(--green)"/><path d="M3 6l2 2 4-4" fill="none" stroke="#fff" stroke-width="1.5"/></svg>
  <span class="doc-tab" style="left:148px">Lines</span>
  <span class="doc-tab" style="left:232px">Changes</span>
  <svg style="left:319px;top:9px" width="12" height="12"><circle cx="6" cy="6" r="6" fill="var(--green)"/><path d="M3 6l2 2 4-4" fill="none" stroke="#fff" stroke-width="1.5"/></svg>
  <span class="doc-tab" style="left:344px">Notes</span>
</div>

<div class="a actionbar">
  <svg style="left:20px;top:6px" width="22" height="18"><rect x="1" y="1" width="18" height="13" fill="none" stroke="#fff" stroke-width="1.6"/><path d="M1 5h18M4 9h8" stroke="#fff" stroke-width="1.6"/><circle cx="19" cy="14" r="4" fill="var(--green)"/></svg>
  <span class="a" style="left:50px">Post Order</span>
  <svg style="left:817px;top:6px" width="17" height="17"><circle cx="7" cy="7" r="6" fill="none" stroke="#fff" stroke-width="1.5"/><path d="M11 11l5 5" stroke="#fff" stroke-width="1.5"/></svg>
  <span class="a" style="left:843px">search</span>
  <svg style="left:904px;top:7px" width="16" height="16"><path d="M8 0v16M0 8h16" stroke="#fff" stroke-width="1.3"/></svg>
  <span class="a" style="left:927px">new</span>
  <svg style="left:971px;top:5px" width="18" height="18"><path d="M6 2L2 6l4 4M2 6h8a6 6 0 010 12H7" fill="none" stroke="#fff" stroke-width="2"/></svg>
  <span class="a" style="left:995px">back</span>
  <svg style="left:1043px;top:7px" width="20" height="16"><path d="M1 8l6 6L19 1" fill="none" stroke="var(--green)" stroke-width="2.5"/></svg>
  <span class="a" style="left:1068px;color:var(--green)">apply</span>
  <svg style="left:1120px;top:6px" width="16" height="16"><path d="M1 1l14 14M15 1L1 15" stroke="var(--red)" stroke-width="2.5"/></svg>
  <span class="a" style="left:1145px;color:var(--red)">delete</span>
</div>

<main>
  <span class="a lbl r" style="left:20px;top:276px;width:65px">Order #</span>
  <span class="a" style="left:111px;top:277px;font-size:12.5px">100159</span>

  <span class="a lbl r" style="left:10px;top:312px;width:75px">Ship from</span>
  <div class="field" style="left:101px;top:308px;width:105px">1001</div>
  <span class="a link" style="left:215px;top:311px">/</span>
  <div class="field" style="left:230px;top:308px;width:33px">0</div>

  <div class="field focus" style="left:101px;top:345px;width:280px">Harbor Clinical Goods|</div>
  <svg style="left:393px;top:347px" width="22" height="22"><circle cx="11" cy="11" r="10" fill="none" stroke="var(--blue-dark)" stroke-width="1.3"/><ellipse cx="11" cy="11" rx="4.5" ry="10" fill="none" stroke="var(--blue-dark)" stroke-width="1.3"/><path d="M1 11h20M3 6h16M3 16h16" stroke="var(--blue-dark)" stroke-width="1.1"/></svg>

  <span class="a lbl r" style="left:10px;top:384px;width:75px">Address</span>
  <div class="field" style="left:101px;top:381px;width:280px">14 Alder Lane</div>
  <div class="field" style="left:101px;top:417px;width:280px"></div>
  <span class="a link" style="left:399px;top:420px">DPV Unconfirmed</span>

  <span class="a lbl r" style="left:10px;top:456px;width:75px">City</span>
  <div class="field" style="left:101px;top:453px;width:203px">Millbrook</div>
  <span class="a lbl" style="left:322px;top:456px">State</span>
  <div class="field" style="left:370px;top:453px;width:43px">NY</div>
  <svg style="left:424px;top:458px" width="16" height="16"><rect x="1" y="1" width="14" height="14" rx="3" fill="none" stroke="var(--green)" stroke-width="1.5"/><path d="M4 8l3 3 5-6" fill="none" stroke="var(--green)" stroke-width="1.6"/></svg>
  <span class="a" style="left:446px;top:456px;font-size:14.5px;color:var(--green)">Accept</span>

  <span class="a lbl r" style="left:10px;top:493px;width:75px">Zip</span>
  <div class="field" style="left:101px;top:490px;width:114px">12545-1180</div>
  <span class="a lbl" style="left:231px;top:493px">Country</span>
  <div class="field" style="left:297px;top:490px;width:115px">US</div>
  <span class="a link" style="left:437px;top:493px;text-decoration:underline">Add Contact</span>
</main>

<section class="a panel"></section>
<span class="a section-tab" style="left:27px">Order Info</span>
<span class="a section-tab active" style="left:125px">Shipping</span>
<div class="a" style="left:125px;top:566px;width:59px;height:4px;background:var(--blue-dark)"></div>
<span class="a section-tab" style="left:213px">Payment</span>
<span class="a section-tab" style="left:302px">Accounts</span>
<span class="a section-tab" style="left:393px">Totals / Approval</span>

<span class="a lbl r" style="left:0;top:589px;width:132px">Receive At</span>
<div class="field select" style="left:142px;top:586px;width:151px;height:24px;padding-top:4px">ALCH</div>
<span class="a lbl r" style="left:0;top:622px;width:132px">Carrier</span>
<div class="field select" style="left:142px;top:619px;width:151px;height:24px;padding-top:4px">ParcelJet</div>
<span class="a lbl r" style="left:0;top:655px;width:132px">Express Service</span>
<div class="field select" style="left:142px;top:653px;width:151px;height:24px"></div>
<span class="a lbl r" style="left:0;top:688px;width:132px">FOB</span>
<div class="field select" style="left:142px;top:686px;width:151px;height:24px"></div>
<span class="a lbl r" style="left:0;top:723px;width:132px">Order Ship Rule</span>
<div class="field select" style="left:142px;top:721px;width:192px;height:24px;padding-top:4px">Partials</div>
<span class="a lbl r" style="left:0;top:757px;width:132px">Line Ship Rule</span>
<div class="field select" style="left:142px;top:755px;width:192px;height:24px;padding-top:4px">Partials</div>

<span class="a lbl r" style="left:300px;top:589px;width:132px">Request Date</span>
<div class="field" style="left:442px;top:586px;width:151px;height:24px;padding-top:4px">01/07/2018</div>
<svg style="left:570px;top:589px" width="18" height="18"><rect x="1" y="3" width="16" height="14" fill="none" stroke="#666" stroke-width="1.5"/><path d="M1 7h16M5 1v4M13 1v4M5 10h2M9 10h2M13 10h1M5 13h2M9 13h2" stroke="#666" stroke-width="1.5"/></svg>
<span class="a lbl r" style="left:300px;top:622px;width:132px">Freight Terms</span>
<div class="field select" style="left:442px;top:619px;width:151px;height:24px;padding-top:4px">Collect</div>
<span class="a lbl r" style="left:300px;top:655px;width:132px">Freight Calc</span>
<div class="field select" style="left:442px;top:653px;width:193px;height:24px"></div>

<span class="a lbl" style="left:655px;top:586px">Customer Ship To</span>
<div class="field" style="left:784px;top:584px;width:105px;height:26px"></div>
<span class="a link" style="left:898px;top:586px">/</span>
<div class="field" style="left:913px;top:584px;width:33px;height:26px"></div>

<svg style="left:1110px;top:721px" width="22" height="30"><path d="M5 12V7a6 6 0 0112 0v5" fill="none" stroke="var(--orange)" stroke-width="1.5"/><rect x="1" y="12" width="20" height="16" fill="none" stroke="var(--orange)" stroke-width="1.5"/><path d="M1 23h20" stroke="var(--orange)" stroke-width="1"/><text x="11" y="22" text-anchor="middle" font-size="8" fill="var(--orange)" font-family="Open Sans,sans-serif">0</text></svg>

<div class="a footer-rule"></div>
<footer>
  <svg style="left:16px;top:824px" width="26" height="26"><path d="M20 8L9 19a3 3 0 01-4-4L17 3a2 2 0 013 3L8 18" fill="none" stroke="var(--blue-dark)" stroke-width="1.6"/></svg>
  <svg style="left:61px;top:822px" width="26" height="30"><path d="M2 1h13l5 5v22H2z" fill="none" stroke="var(--blue-dark)" stroke-width="1.5"/><path d="M6 10h10M6 14h10M6 18h6" stroke="var(--blue-dark)" stroke-width="1.3"/><circle cx="17" cy="21" r="4" fill="#fff" stroke="var(--blue-dark)" stroke-width="1.5"/><path d="M20 24l4 4" stroke="var(--blue-dark)" stroke-width="1.5"/></svg>
  <svg style="left:104px;top:824px" width="26" height="26"><path d="M6 13L20 5M6 13l14 8" stroke="var(--blue-dark)" stroke-width="2"/><circle cx="6" cy="13" r="4.5" fill="var(--blue-dark)"/><circle cx="20" cy="5" r="4.5" fill="var(--blue-dark)"/><circle cx="20" cy="21" r="4.5" fill="var(--blue-dark)"/></svg>
  <svg style="left:155px;top:823px" width="29" height="28"><rect x="1" y="6" width="27" height="20" fill="none" stroke="var(--blue-dark)" stroke-width="1.5"/><path d="M10 6V2h9v4M1 13h27M8 11v5M21 11v5" stroke="var(--blue-dark)" stroke-width="1.5"/></svg>
  <svg style="left:207px;top:821px" width="30" height="30"><circle cx="15" cy="15" r="14" fill="none" stroke="#666" stroke-width="1.6"/><text x="15" y="22" text-anchor="middle" font-size="19" fill="#666" font-family="Open Sans,sans-serif">?</text></svg>
  <span class="a status">Enter property values, and click Apply</span>
</footer>

</body>
</html>
```